Modern Business Card

Modern professional business card with more than just logo and demographic info. Something memorable.

We are a trendy/modern chiropractic group with an emphasis on neurology, hence the minimalist-type brain logo. We want to convey that modern and technical aspect with professionalism and the elite nature of our practice environment.

```html
<!DOCTYPE html>
<html lang="en">
<head>
<meta charset="utf-8">
<title>Vantage Chiropractic – Business Card</title>
<link href="https://fonts.googleapis.com/css2?family=Roboto:wght@400;700&display=swap" rel="stylesheet">
<style>
  :root{
    --bg:#e9e6df;
    --ink:#000000;
    --paper:#f4f4f5;
    --blue:#3f74c0;
    --white:#ffffff;
    --dark-text:#1a1a1a;
    --muted:#cfcfcf;
  }
  *{margin:0;padding:0;box-sizing:border-box}
  html,body{width:1200px;height:960px;overflow:hidden;background:var(--bg);font-family:"Roboto",Arial,sans-serif}
  .canvas{width:1200px;height:960px;display:flex;flex-direction:column;align-items:center;justify-content:space-evenly}
  .card{width:770px;height:440px;position:relative;overflow:hidden;box-shadow:0 6px 18px rgba(0,0,0,.18)}
  .card-front{background:var(--ink);display:flex;align-items:center;justify-content:center}
  .brand{display:flex;align-items:center;gap:22px}
  .brand-mark{width:54px;height:54px;background:var(--blue)}
  .brand-name{font-weight:400;letter-spacing:.08em;line-height:1.05;text-transform:uppercase}
  .card-front .brand-name{color:var(--white);font-size:40px}
  .card-back{background:var(--paper)}
  .card-back .wave{position:absolute;inset:0}
  .card-back .brand{position:absolute;top:40px;right:60px;gap:16px}
  .card-back .brand-mark{width:44px;height:44px}
  .card-back .brand-name{color:var(--dark-text);font-size:32px}
  .contact{position:absolute;left:60px;bottom:40px;color:var(--white)}
  .contact-name{color:var(--blue);font-weight:700;font-size:30px;line-height:1.2}
  .contact-role{font-size:16px;color:var(--muted);margin:2px 0 12px}
  .contact-list{list-style:none;font-size:17px;line-height:1.65}
  .contact-list li{display:flex;align-items:center;gap:12px}
  .contact-list svg{width:16px;height:16px;flex:none;fill:none;stroke:var(--blue);stroke-width:2}
</style>
</head>
<body>
<main class="canvas">
  <section class="card card-front">
    <div class="brand">
      <span class="brand-mark"></span>
      <span class="brand-name">Vantage<br>Chiropractic</span>
    </div>
  </section>

  <section class="card card-back">
    <svg class="wave" viewBox="0 0 770 440" preserveAspectRatio="none">
      <path d="M0 135 C 150 95, 350 210, 560 215 C 660 218, 720 205, 770 175 L770 440 L0 440 Z" fill="var(--ink)"/>
      <path d="M0 127 C 150 87, 350 202, 560 207 C 660 210, 720 197, 770 167" fill="none" stroke="var(--blue)" stroke-width="5"/>
    </svg>
    <div class="brand">
      <span class="brand-mark"></span>
      <span class="brand-name">Vantage<br>Chiropractic</span>
    </div>
    <div class="contact">
      <p class="contact-name">Marcus Hale</p>
      <p class="contact-role">Owner</p>
      <ul class="contact-list">
        <li><svg viewBox="0 0 16 16"><path d="M3 2l3 0 1 4-2 1c1 2 2 3 4 4l1-2 4 1 0 3c-7 0-11-4-11-11z"/></svg>(555) 310-4827</li>
        <li><svg viewBox="0 0 16 16"><rect x="1.5" y="3.5" width="13" height="9"/><path d="M1.5 3.5l6.5 5 6.5-5"/></svg>hello@vantagespine.com</li>
        <li><svg viewBox="0 0 16 16"><circle cx="8" cy="8" r="6.5"/><path d="M1.5 8h13M8 1.5c-3 3.5-3 9.5 0 13M8 1.5c3 3.5 3 9.5 0 13"/></svg>www.vantagespine.com</li>
        <li><svg viewBox="0 0 16 16"><path d="M8 15s5-5 5-8.5A5 5 0 0 0 3 6.5C3 10 8 15 8 15z"/><circle cx="8" cy="6.5" r="1.8"/></svg>Harlow Park Rd. Brookfield, OH 45012</li>
      </ul>
    </div>
  </section>
</main>
</body>
</html>
```